Business Card Design - Amberfield Court

We are looking at a new design for our business cards that has a modern and professional look. We run a residential aged care facility focussing on the care of residents. The cards will be used for potential clients, consultants and business opportunities in this sector. Blue and white is our main colours and would to see these colours incorporated in the design.
Industry/Entity Type
Business
Contact Information for Business Card
Amberfield Court, Darren Walsh, dwalsh@amberfieldcourt.com.au, Finance Manager, 0472 639 208, BCom, 37 Marrabel Crescent, Brindle Vale, Qld 4093.
Look and feel
Each slider illustrates characteristics of the customer's brand and the style your logo design should communicate.

```html
<!DOCTYPE html>
<html lang="en">
<head>
<meta charset="utf-8">
<title>Amberfield Court – Business Card</title>
<link href="https://fonts.googleapis.com/css2?family=Open+Sans:wght@400;700;800&display=swap" rel="stylesheet">
<style>
  :root {
    --page-bg: #e9eaec;
    --card-blue: #4a7c98;
    --band-navy: #1f3c4e;
    --taupe: #ada39b;
    --white: #ffffff;
    --logo-navy: #2b4c60;
  }
  * { box-sizing: border-box; margin: 0; padding: 0; }
  html, body { width: 1200px; height: 900px; overflow: hidden; }
  body {
    background: var(--page-bg);
    font-family: "Open Sans", Arial, sans-serif;
    position: relative;
  }
  .card {
    position: absolute;
    width: 700px;
    height: 400px;
    border-radius: 26px;
    overflow: hidden;
    box-shadow: 0 10px 28px rgba(0,0,0,0.18);
  }
  /* Back side */
  .card-back {
    left: 120px; top: 40px;
    background: var(--taupe);
    display: flex; align-items: center; justify-content: center;
  }
  .card-back .brand-name {
    color: var(--white);
    font-weight: 700;
    font-size: 46px;
    letter-spacing: 1px;
  }
  /* Front side */
  .card-front {
    left: 380px; top: 460px;
    background: var(--card-blue);
    color: var(--white);
  }
  .side-band {
    position: absolute; left: 0; top: 0;
    width: 96px; height: 100%;
    background: var(--band-navy);
  }
  .rule-vertical {
    position: absolute; left: 110px; top: 0;
    width: 3px; height: 100%;
    background: var(--white);
  }
  .rule-horizontal {
    position: absolute; left: 110px; top: 118px;
    width: 590px; height: 3px;
    background: var(--white);
  }
  .brand-lockup {
    position: absolute; left: 22px; top: 34px;
    display: flex; align-items: center; gap: 10px;
    background: var(--card-blue);
    padding: 10px 14px;
  }
  .brand-mark {
    width: 18px; height: 18px;
    background: var(--logo-navy);
    flex: none;
  }
  .brand-lockup .brand-name {
    color: var(--logo-navy);
    font-weight: 700;
    font-size: 22px;
    white-space: nowrap;
  }
  .contact {
    position: absolute; left: 140px; top: 150px;
  }
  .person-name {
    font-weight: 800;
    font-size: 30px;
    letter-spacing: 0.5px;
    line-height: 1.1;
  }
  .person-role {
    font-size: 16px;
    letter-spacing: 0.5px;
    margin-bottom: 14px;
  }
  .address-line, .contact-line {
    font-size: 17px;
    line-height: 1.4;
  }
  .address { margin-bottom: 8px; }
  .contact-line { display: flex; align-items: center; gap: 8px; }
  .contact-line svg { width: 14px; height: 14px; flex: none; }
</style>
</head>
<body>
  <section class="card card-back" aria-label="Card back">
    <span class="brand-name">Amberfield Court</span>
  </section>

  <section class="card card-front" aria-label="Card front">
    <div class="side-band"></div>
    <div class="rule-vertical"></div>
    <div class="rule-horizontal"></div>

    <div class="brand-lockup">
      <span class="brand-mark" aria-hidden="true"></span>
      <span class="brand-name">Amberfield Court</span>
    </div>

    <div class="contact">
      <div class="person-name">DARREN WALSH</div>
      <div class="person-role">FINANCE MANAGER (BCOM)</div>
      <div class="address">
        <div class="address-line">37 Marrabel Crescent</div>
        <div class="address-line">Brindle Vale, Qld 4093</div>
      </div>
      <div class="contact-line">
        <svg viewBox="0 0 24 24" aria-hidden="true"><path fill="#fff" d="M6.6 10.8a15.1 15.1 0 0 0 6.6 6.6l2.2-2.2a1 1 0 0 1 1-.25 11.4 11.4 0 0 0 3.6.57 1 1 0 0 1 1 1V20a1 1 0 0 1-1 1A17 17 0 0 1 3 4a1 1 0 0 1 1-1h3.5a1 1 0 0 1 1 1c0 1.25.2 2.45.57 3.57a1 1 0 0 1-.25 1z"/></svg>
        <span>0472 639 208</span>
      </div>
      <div class="contact-line">
        <svg viewBox="0 0 24 24" aria-hidden="true"><rect x="2.5" y="5" width="19" height="14" rx="1.5" fill="none" stroke="#fff" stroke-width="2"/><path d="M3 6l9 7 9-7" fill="none" stroke="#fff" stroke-width="2"/></svg>
        <span>dwalsh@amberfieldcourt.com.au</span>
      </div>
    </div>
  </section>
</body>
</html>
```